The Brandwell Firm

We need a new design for our letterhead and envelopes. We are a personal injury and criminal defense firm so we need something modern and clean, but more on the professional/traditional side. Our new logo has two colors and is attached to the file so we need something that works well with those colors/matches the design. The following information needs to be on the letterhead:
Phone: (555) 214-3370
Fax: (555) 214-5186
Toll-Free: (888) 431-2059
Post Office Box 4721
Millbrook, SC 29555-4721
HarmClaimCounsel.example
PalmettoTrialAdvocates.example

Target Market(s)

Clients, government agencies, other law firms

Industry/Entity Type

Legal

Font styles to use
Sans Serif
Other font styles liked:
• Arial

Colors

Designer to choose colors to be used in the design.

Requirements
Must have
• Must look professional and clean, modern
Nice to have
• I would like to see a design that works with the logo but does not distract from the content that will be printed on it
Should not have
• Too many colors or crazy designs.

```html
<!DOCTYPE html>
<html lang="en">
<head>
<meta charset="utf-8">
<title>The Brandwell Firm — Stationery</title>
<link rel="stylesheet" href="https://fonts.googleapis.com/css2?family=Open+Sans:wght@400;600&display=swap">
<style>
  :root {
    --navy: #2e3192;
    --red: #d7282f;
    --ink: #3a3a3a;
    --paper: #ffffff;
    --backdrop: #efefef;
    --edge: #dcdcdc;
  }
  * { margin: 0; padding: 0; box-sizing: border-box; }
  html, body { width: 1155px; height: 1200px; overflow: hidden; }
  body {
    position: relative;
    background: var(--backdrop);
    font-family: "Open Sans", Arial, sans-serif;
    color: var(--ink);
  }
  .sheet {
    position: absolute;
    background: var(--paper);
    border: 1px solid var(--edge);
  }
  .letterhead { left: 81px; top: 188px; width: 614px; height: 807px; }
  .brand {
    position: absolute;
    display: flex;
    align-items: center;
    gap: 8px;
  }
  .brand-mark { width: 12px; height: 12px; background: var(--red); flex: none; }
  .brand-name {
    font-weight: 600;
    color: var(--navy);
    white-space: nowrap;
    letter-spacing: 0.2px;
  }
  .letterhead .brand { left: 42px; top: 64px; }
  .letterhead .brand-name { font-size: 19px; }
  .contact-block {
    position: absolute;
    left: 427px; top: 50px;
    border-left: 1px solid var(--navy);
    padding-left: 12px;
    height: 81px;
    font-size: 9px;
    line-height: 1.3;
  }
  .contact-block .address { margin-bottom: 5px; }
  .contact-line { display: flex; align-items: center; gap: 4px; height: 12px; }
  .contact-line svg { width: 8px; height: 8px; flex: none; }

  .envelope-back { left: 558px; top: 387px; width: 553px; height: 252px; }
  .flap { position: absolute; left: 0; top: 0; width: 553px; height: 71px; display: block; }
  .flap-name {
    position: absolute; left: 0; top: 24px; width: 553px;
    text-align: center; font-size: 11px; font-weight: 600;
    color: var(--paper); letter-spacing: 0.3px;
  }

  .envelope-front { left: 558px; top: 670px; width: 553px; height: 253px; }
  .envelope-front .brand { left: 27px; top: 48px; }
  .envelope-front .brand-name { font-size: 16px; }
  .envelope-front .brand-mark { width: 10px; height: 10px; }
  .return-address {
    position: absolute; left: 26px; top: 217px;
    font-size: 7.5px; line-height: 1.25;
  }
</style>
</head>
<body>
  <section class="sheet letterhead" aria-label="Letterhead">
    <div class="brand">
      <span class="brand-mark"></span>
      <span class="brand-name">The Brandwell Firm</span>
    </div>
    <address class="contact-block" style="font-style:normal">
      <p class="address">P.O.&nbsp; Box 4721 Millbrook,<br>SC 29555-4721</p>
      <p class="contact-line">
        <svg viewBox="0 0 10 10"><path fill="#d7282f" d="M2 0.5 3.6 2.6 2.7 3.7c.6 1.4 1.9 2.7 3.4 3.4l1.1-.9L9.5 8 8.4 9.5C4.2 9.2.8 5.8.5 1.6z"/></svg>
        (555) 214-3370
      </p>
      <p class="contact-line">
        <svg viewBox="0 0 10 10"><rect x="2.5" y="0.5" width="5" height="3" fill="#d7282f"/><rect x="0.5" y="3.5" width="9" height="4" rx="1" fill="#d7282f"/><rect x="2.5" y="6" width="5" height="3.5" fill="#fff" stroke="#d7282f"/></svg>
        (555) 214-5186
      </p>
      <p class="contact-line">
        <svg viewBox="0 0 10 10"><path fill="#d7282f" d="M2 0.5 3.6 2.6 2.7 3.7c.6 1.4 1.9 2.7 3.4 3.4l1.1-.9L9.5 8 8.4 9.5C4.2 9.2.8 5.8.5 1.6z"/></svg>
        (888) 431-2059 (Toll-Free)
      </p>
      <p class="contact-line">
        <svg viewBox="0 0 10 10" fill="none" stroke="#d7282f" stroke-width="0.9"><circle cx="5" cy="5" r="4.3"/><ellipse cx="5" cy="5" rx="1.8" ry="4.3"/><path d="M0.7 5h8.6M1.5 2.8h7M1.5 7.2h7"/></svg>
        HarmClaimCounsel.example
      </p>
      <p class="contact-line">
        <svg viewBox="0 0 10 10" fill="none" stroke="#d7282f" stroke-width="0.9"><circle cx="5" cy="5" r="4.3"/><ellipse cx="5" cy="5" rx="1.8" ry="4.3"/><path d="M0.7 5h8.6M1.5 2.8h7M1.5 7.2h7"/></svg>
        PalmettoTrialAdvocates.example
      </p>
    </address>
  </section>

  <section class="sheet envelope-back" aria-label="Envelope back">
    <svg class="flap" viewBox="0 0 553 71" aria-hidden="true">
      <path fill="#2e3192" d="M0 0H553L543 56Q540 71 524 71H30Q12 71 10 56Z"/>
    </svg>
    <p class="flap-name">The Brandwell Firm</p>
  </section>

  <section class="sheet envelope-front" aria-label="Envelope front">
    <div class="brand">
      <span class="brand-mark"></span>
      <span class="brand-name">The Brandwell Firm</span>
    </div>
    <p class="return-address">P.O.&nbsp; Box 4721 Millbrook,<br>SC 29555-4721</p>
  </section>
</body>
</html>
```